Market Research firm needs updated business cards with new logo

We need the logo to be included somewhere on the card (attached). We would also like the phrases "Independent, Objective, Comprehensive" and "Research You Can Trust" somewhere on the card. Front or back. Our colors are hex codes 6075a7, e48d25 and 5a5b5b. Though you are certainly not limited to those shades, whatever you produce should coordinate with them. I have also attached our favicon. Feel free to use it in your design, but please do not use it to replace the full logo.

Contact Information for Business Card

see project description

Font styles to use
Other font styles liked:
• Open Sans

Requirements
Must have
• the logo
• We use Open Sans font

```html
<!DOCTYPE html>
<html lang="en">
<head>
<meta charset="utf-8">
<title>Quorra Research – Business Card</title>
<link href="https://fonts.googleapis.com/css2?family=Open+Sans:wght@400;600;700&display=swap" rel="stylesheet">
<style>
  :root {
    --stage: #000000;
    --card: #5a5b5b;
    --orange: #e48d25;
    --blue: #6075a7;
    --white: #ffffff;
    --mark-tint: rgba(228, 141, 37, 0.28);
  }
  * { box-sizing: border-box; margin: 0; padding: 0; }
  html, body {
    width: 1200px; height: 1200px; overflow: hidden;
    background: var(--stage);
    font-family: "Open Sans", Arial, sans-serif;
  }
  .card {
    position: absolute; width: 840px; height: 480px;
    background: var(--card); overflow: hidden;
  }
  .card--front { left: 178px; top: 94px; }
  .card--back { left: 180px; top: 625px; }

  .brand-name {
    position: absolute; color: var(--orange);
    font-weight: 600; white-space: nowrap; letter-spacing: -0.5px; line-height: 1.2;
  }
  .card--front .brand-name { right: 92px; top: 48px; font-size: 38px; }
  .card--back .brand-name {
    left: 0; right: 0; text-align: center; top: 185px; font-size: 70px;
  }

  .brand-backdrop {
    position: absolute; left: 520px; top: 135px;
    width: 330px; height: 330px; border-radius: 50%;
    background: radial-gradient(circle, var(--mark-tint) 0%, rgba(228,141,37,0.18) 55%, rgba(228,141,37,0) 72%);
  }

  .holder-name {
    position: absolute; left: 38px; top: 242px;
    color: var(--orange); font-weight: 700; font-size: 40px;
    line-height: 1; letter-spacing: 0.5px; white-space: nowrap;
  }
  .holder-role {
    position: absolute; left: 38px; top: 291px;
    color: var(--orange); font-size: 25px; line-height: 1; white-space: nowrap;
  }
  .divider {
    position: absolute; left: 124px; right: 0; top: 304px;
    border-top: 2px dotted rgba(255,255,255,0.75);
  }

  .contact-list { position: absolute; left: 32px; top: 328px; list-style: none; }
  .contact-item {
    display: flex; align-items: flex-start; gap: 8px;
    color: var(--white); font-size: 20px; line-height: 23px; margin-bottom: 7px;
  }
  .contact-item svg { flex: 0 0 20px; width: 20px; height: 22px; margin-top: 2px; }

  .band-thin {
    position: absolute; left: 0; top: 439px; width: 540px; height: 9px;
    background: var(--blue); border-radius: 0 4px 4px 0;
  }
  .band-base {
    position: absolute; left: 0; bottom: 0; width: 100%; height: 24px;
    background: var(--blue);
  }
  .web-tab {
    position: absolute; right: 0; bottom: 0; width: 298px; height: 50px;
    background: var(--blue);
    clip-path: polygon(8px 0, 100% 0, 100% 100%, 0 100%);
    border-radius: 4px 0 0 0;
    color: var(--white); font-size: 28px; line-height: 50px;
    padding-left: 22px; white-space: nowrap;
  }

  .tagline {
    position: absolute; top: 296px; color: var(--orange);
    font-size: 21px; line-height: 28px; letter-spacing: 0.2px; white-space: nowrap;
  }
  .tagline--one { left: 46px; }
  .tagline--two { left: 236px; }
  .tagline--three { left: 478px; }
</style>
</head>
<body>

<section class="card card--front">
  <div class="brand-backdrop" role="img" aria-label="Faint brand symbol decoration"></div>
  <div class="brand-name">Quorra Research</div>

  <h1 class="holder-name">JOHN SMITH</h1>
  <div class="holder-role">Owner</div>
  <div class="divider"></div>

  <ul class="contact-list">
    <li class="contact-item">
      <svg viewBox="0 0 20 20" aria-hidden="true"><circle cx="10" cy="10" r="10" fill="#6075a7"/><path d="M6.5 5.5l2 0 1 2.5-1.3 1c.6 1.2 1.6 2.2 2.8 2.8l1-1.3 2.5 1v2c0 .6-.5 1-1 1C9 14.3 5.7 11 5.5 6.5c0-.5.4-1 1-1z" fill="#5a5b5b"/></svg>
      <span>455 555 555</span>
    </li>
    <li class="contact-item">
      <svg viewBox="0 0 20 20" aria-hidden="true"><rect x="1" y="5" width="18" height="12" fill="none" stroke="#6075a7" stroke-width="1.4"/><path d="M1 5l9 7 9-7M1 17l6.5-6M19 17l-6.5-6" fill="none" stroke="#6075a7" stroke-width="1.4"/></svg>
      <span>youremail@gmail.com</span>
    </li>
    <li class="contact-item">
      <svg viewBox="0 0 20 26" aria-hidden="true"><path d="M10 1a8 8 0 0 0-8 8c0 6 8 16 8 16s8-10 8-16a8 8 0 0 0-8-8z" fill="#6075a7"/><circle cx="10" cy="9" r="3" fill="#5a5b5b"/></svg>
      <span>your location and<br>zip address</span>
    </li>
  </ul>

  <div class="band-thin"></div>
  <div class="band-base"></div>
  <div class="web-tab">www.yourweb.com</div>
</section>

<section class="card card--back">
  <div class="brand-name">Quorra Research</div>
  <p class="tagline tagline--one">INDEPENDENT</p>
  <p class="tagline tagline--two">COMPREHENSIVE</p>
  <p class="tagline tagline--three">RESEARCH YOU CAN TRUST</p>
</section>

</body>
</html>
```